Coral Slumber Depot Website

Need a design for a local Miami mattress store.
The store is called Coral Slumber Depot.
need it to be something that customers can find on the internet and will
give them my location, they need to know i have the same brand mattress as the other store except i have them at almost half the price.

the office phone number is (786)413-9067
the office address is: 24517 sw Heron Glade Ln, Miami FL 33189

included is the logo, id like to stick the with white and teal design

here are is an excerpt that can or cannot be included

"We are a premium mattress discount outlet store located in South Florida; offering Free Delivery to Broward Miami-Dade, the Keys, and Palm Beach.

We carry the best brands in the market: Kellard DreamLoft; Brodin SpineEase, Whitcombe & Lyle, Pardue, among others.

We are open 7 days a week, and we are accessible from all major highways. We are a family business and our goal is to provide you with the most comfortable and best quality mattress at a price that has no competition. Come visit us and take a look at our large inventory selection."

```html
<!DOCTYPE html>
<html lang="en">
<head>
<meta charset="utf-8">
<title>Coral Slumber Depot</title>
<link href="https://fonts.googleapis.com/css2?family=Federo&family=Oswald:wght@500&family=Arimo:wght@400;700&family=Montserrat:wght@500&display=swap" rel="stylesheet">
<style>
:root{
  --teal:#1bb5d8;
  --teal-light:#5fd3ee;
  --teal-text:#24a9cc;
  --page:#f1efec;
  --panel:#ecebe8;
  --ink:#333;
  --body:#4a4a4a;
  --navy:#1c2f6b;
  --footer:#3b3b3b;
  --footer-text:#cfcfcf;
  --red:#d42a2a;
}
*{margin:0;padding:0;box-sizing:border-box}
html,body{width:766px;height:1200px;overflow:hidden}
body{position:relative;background:var(--page);font-family:"Arimo",Arial,sans-serif;color:var(--ink)}
.abs{position:absolute}
.header-band{left:0;top:0;width:766px;height:282px;background:radial-gradient(circle at 20% 40%,var(--teal-light),transparent 45%),radial-gradient(circle at 85% 15%,#46c9e6,transparent 40%),linear-gradient(180deg,#17b2d6,#20bddf)}
.brand{left:66px;top:46px;display:flex;align-items:center;gap:8px;color:#fff;font-family:"Federo",serif;font-size:19px;letter-spacing:.5px}
.brand-mark{width:12px;height:12px;background:#fff}
.nav{left:350px;top:63px;display:flex;align-items:center;font-family:"Montserrat",sans-serif;font-size:7.6px;color:#123;text-transform:uppercase}
.nav a{color:#0e2a38;text-decoration:none;padding:0 8.5px;line-height:24px}
.nav a.active{background:#fff;border-radius:2px;padding:0 15px;margin-right:1px}
.hero{left:63px;top:118px;width:639px;height:259px;background:#fff;padding:4px;box-shadow:0 8px 14px rgba(0,0,0,.15)}
.hero-photo{width:100%;height:100%;background:linear-gradient(100deg,#e9e7e2 0%,#d9d7d2 45%,#cfc8c0 70%,#b89c86 100%)}
.hero-copy{left:361px;top:278px}
.hero-copy p{font-family:"Oswald",sans-serif;font-size:20px;line-height:25px;color:#fff;text-shadow:0 1px 2px rgba(0,0,0,.45)}
.hero-copy p.red{color:var(--red)}
.hero-copy p.teal{font-family:"Federo",serif;color:var(--teal);font-size:16px;letter-spacing:.5px;text-shadow:none}
.intro{left:75px;top:420px;width:625px}
.intro h1{font-family:"Federo",serif;font-weight:400;font-size:14.5px;line-height:19px;color:var(--teal-text);letter-spacing:.7px;text-transform:uppercase;margin-bottom:9px}
.intro p{font-size:7.9px;line-height:14px;color:var(--body);margin-bottom:4px}
.quote-band{left:0;top:620px;width:766px;height:172px;background:linear-gradient(90deg,#dcd4c6,#eee9e1 40%,#ece7de 70%,#cfc6b8)}
.quote-icon{left:93px;top:672px;width:20px;height:20px;border-radius:50%;background:var(--teal);border:2px solid #fff;color:#fff;font:bold 13px/18px Georgia,serif;text-align:center}
.quote-text{left:124px;top:685px;width:590px;font-size:14px;line-height:20px;color:#333}
.btn-read{left:317px;top:738px;width:72px;height:25px;background:var(--teal);color:#fff;font-size:10px;line-height:25px;text-align:center}
.lower{left:0;top:792px;width:766px;height:320px;background:var(--panel)}
.office{left:118px;top:842px;width:135px;height:236px;background:#fff}
.office-bar{height:24px;background:#a3aaa6;display:flex;align-items:center;justify-content:space-between;padding:0 8px;font-size:4.5px;color:#555}
.office-bar i{width:6px;height:6px;border-radius:50%;background:#777;display:block}
.office h3{font-weight:400;font-size:11.5px;color:#555;margin:19px 0 0 11px}
.office-map{left:14px;top:70px;width:86px;height:52px;background:linear-gradient(180deg,#c4c4c4,#aaaaaa);opacity:.8}
.office-addr{left:12px;top:134px;font-size:8px;line-height:12px;color:#444}
.office-addr strong{color:var(--navy);display:block}
.btn-spot{left:15px;top:204px;width:61px;height:12px;background:#3a3a3a;color:#fff;font-size:6px;line-height:12px;padding-left:5px}
.brands{left:273px;top:842px;width:385px;height:234px;background:#eeeeec;border:1px solid #dcdcdc;border-radius:4px}
.brands h2{font-family:"Federo",serif;font-weight:400;font-size:14px;letter-spacing:1px;color:#333;text-align:center;margin-top:20px}
.tile{width:131px;height:68px;border:2px solid #fff;display:flex;align-items:center;justify-content:center;font-family:"Federo",serif;font-size:12px;text-align:center}
.t1{left:43px;top:47px;background:#b60b30;color:#fff}
.t2{left:185px;top:47px;background:#e9f3fb;color:#1d3f7b}
.t3{left:43px;top:123px;background:#f1dcae;color:#4a3a1a}
.t4{left:187px;top:123px;background:#a9a9a9;color:#3d3d3d;font-size:16px;letter-spacing:1px}
.view-more{left:252px;top:206px;font-size:11px;color:var(--teal-text)}
.footer{left:0;top:1112px;width:766px;height:88px;background:var(--footer);color:var(--footer-text)}
.footer-links{left:80px;top:13px;display:flex;font-size:7px;gap:0}
.footer-links span{margin-right:9px}
.footer-links span.sep{margin-right:9px}
.follow{left:80px;top:36px;font-size:11px}
.social{left:82px;top:54px;display:flex;gap:9px}
.social i{width:16px;height:16px;border-radius:50%;background:#d6d6d6;display:block}
.footer-note{left:201px;top:42px;font-size:7.6px;letter-spacing:.2px}
</style>
</head>
<body>
<div class="abs header-band"></div>
<div class="abs brand"><span class="brand-mark"></span>Coral Slumber Depot</div>
<nav class="abs nav">
  <a class="active" href="#">Home</a><a href="#">We Are Mattress</a><a href="#">Discounters</a><a href="#">Location</a><a href="#">Get In Touch</a>
</nav>

<div class="abs hero"><div class="hero-photo" role="img" aria-label="Photo of a smiling woman leaning on a white quilted mattress"></div></div>
<div class="abs hero-copy">
  <p>Same Brand Mattress As Other Store</p>
  <p class="red">Except I Have Them At</p>
  <p class="teal">ALMOST HALF THE PRICE</p>
</div>

<section class="abs intro">
  <h1>We are a family business and our goal is to provide you with the most comfortable and best quality mattress at a price that has no competition</h1>
  <p>Based in Stafford, Texas, we design, provide, and service licensed and unlicensed, point-to-point and point-to-multipoint microwave systems. For over 40 years, Relay Span Systems has built and delivered mission critical microwave communications productsLorem Ipsum is simply dummy text of the printing and typesetting industry. Lorem Ipsum has been the industry's standard dummy text ever since the 1500s, when an unknown printer took a galley of type and scrambled it to make a type specimen book. It has survived not only five centuries, but also the leap into electronic typesetting, remaining essentially unchanged.</p>
  <p>Based in Stafford, Texas, we design, provide, and service licensed and unlicensed, point-to-point and point-to-multipoint microwave systems. For over 40 years, Relay Span Systems has built and delivered mission critical microwave communications productsLorem Ipsum is simply dummy text of the printing and typesetting industry. Lorem Ipsum has been the industry's standard dummy text ever since the 1500s, when an unknown printer took a galley of type and scrambled it to make a type specimen book. It has survived not only five centuries, but also the leap into electronic typesetting, remaining essentially unchanged.</p>
</section>

<div class="abs quote-band" role="img" aria-label="Soft-toned photo of a bedroom with a white mattress and cushions"></div>
<div class="abs quote-icon">&ldquo;</div>
<p class="abs quote-text">We are a premium mattress discount outlet store located in South Florida; offering Free Delivery to Broward Miami-Dade, the Keys, and Palm Beach.</p>
<a class="abs btn-read">Read More</a>

<div class="abs lower"></div>
<div class="abs office">
  <div class="office-bar"><i></i><span>01 02 03 04</span></div>
  <h3>Office Location</h3>
  <div class="abs office-map" role="img" aria-label="Grey world map with a location pin"></div>
  <div class="abs office-addr">
    <strong>The Office Address:</strong>
    24517 sw Heron Glade Ln<br>Miami FL 33189<br><span style="display:block;margin-top:2px">Tel: (786)413-9067</span>
  </div>
  <div class="abs btn-spot">Spot Us &nbsp;&nbsp;&nbsp;&nbsp;&nbsp;&nbsp;&nbsp;&nbsp;&rsaquo;</div>
</div>

<div class="abs brands">
  <h2>WE CARRY THE BEST BRANDS IN THE MARKET</h2>
  <div class="abs tile t1">Kellard DreamLoft</div>
  <div class="abs tile t2">Brodin SpineEase</div>
  <div class="abs tile t3">Whitcombe &amp; Lyle</div>
  <div class="abs tile t4">PARDUE</div>
  <span class="abs view-more">View More</span>
</div>

<footer class="abs footer">
  <div class="abs footer-links">
    <span>About Us</span><span class="sep">~</span><span>Categories</span><span class="sep">~</span><span>FAQ's</span><span class="sep">~</span><span>General Conditions of Sale online</span><span class="sep">~</span><span>Shopping Cart</span><span class="sep">~</span><span>Our Partners</span><span class="sep">~</span><span>Contact Us</span><span class="sep">~</span><span>Sitemap</span>
  </div>
  <div class="abs follow">Follow Us on:</div>
  <div class="abs social"><i></i><i></i><i></i></div>
  <p class="abs footer-note">Lorem Ipsum is simply dummy text of the printing and typesetting industry. Lorem Ipsum has been the industry's standard dummy text</p>
</footer>
</body>
</html>
```